High Tech Real Estate Startup needs a business card

We are developing an innovative real estate marketing product based around advanced search and virtual reality.

We talk to people, we need business cards.

Target Market(s)

The target market is technology professionals and realtors.

Contact Information for Business Card

The information to be included will include

Name
Title
Phone Number
E-mail Address
www.zelquin.com

It should use simple iconography for each one of those fields.

Font styles to use
Other font styles liked:
• Co, Jubilat, Avenir

Colors

Designer to choose colors to be used in the design.

Requirements
Must have
• Clean aesthetic,
• Good use of negative space.
• It should use our company logo, shown in the attached file. It is able to use the negative of that logo (coloured font and white background) and I have attached other acceptable accent colours in a swatch file.
Should not have
• Should not be too busy
• No extraneous text (slogans, tag lines etc)

```html
<!DOCTYPE html>
<html lang="en">
<head>
<meta charset="utf-8">
<title>Zelquin Business Card</title>
<link href="https://fonts.googleapis.com/css2?family=Montserrat:wght@500&family=Open+Sans:wght@400;600;700&display=swap" rel="stylesheet">
<style>
  :root {
    --teal: #3aabad;
    --teal-deep: #2b8d90;
    --paper: #f4f4f3;
    --ink: #2a2a2a;
    --stage: #3a3a3a;
    --white: #ffffff;
  }
  html, body {
    margin: 0;
    padding: 0;
    overflow: hidden;
  }
  .canvas {
    width: 799px;
    height: 1200px;
    background: var(--stage);
    position: relative;
    overflow: hidden;
    font-family: "Open Sans", sans-serif;
  }
  .card {
    position: absolute;
    left: 90px;
    width: 620px;
    height: 354px;
    border-radius: 22px;
    overflow: hidden;
  }
  .card-front {
    top: 140px;
    background: var(--teal);
    display: flex;
    align-items: center;
    justify-content: center;
  }
  .brand-name {
    font-family: "Montserrat", sans-serif;
    font-weight: 500;
    letter-spacing: 2px;
    margin: 0;
  }
  .card-front .brand-name {
    font-size: 64px;
    color: var(--teal-deep);
  }
  .card-back {
    top: 706px;
    background: var(--paper);
  }
  .card-back .brand-name {
    position: absolute;
    left: 40px;
    top: 26px;
    font-size: 62px;
    color: var(--teal);
  }
  .waves {
    position: absolute;
    left: 0;
    top: 0;
  }
  .person {
    position: absolute;
    left: 40px;
    top: 118px;
  }
  .person-name {
    margin: 0;
    font-size: 20px;
    font-weight: 700;
    color: var(--ink);
  }
  .person-title {
    margin: 2px 0 0;
    font-size: 11px;
    color: var(--ink);
  }
  .contacts {
    position: absolute;
    right: 22px;
    bottom: 16px;
    list-style: none;
    margin: 0;
    padding: 0;
  }
  .contact-item {
    display: flex;
    justify-content: flex-end;
    align-items: center;
    gap: 8px;
    color: var(--white);
    font-size: 14px;
    line-height: 20px;
  }
  .contact-icon {
    width: 16px;
    height: 16px;
  }
</style>
</head>
<body>
<div class="canvas">

  <section class="card card-front">
    <p class="brand-name">ZELQUIN</p>
  </section>

  <section class="card card-back">
    <svg class="waves" width="620" height="354" viewBox="0 0 620 354">
      <circle cx="0" cy="132" r="14" fill="var(--teal)"/>
      <path d="M0 196 C150 286 320 296 620 196 L620 354 L0 354 Z" fill="var(--teal)"/>
      <path d="M0 214 C150 300 320 306 620 210" fill="none" stroke="var(--white)" stroke-width="7"/>
      <path d="M0 204 C110 250 200 276 300 286" fill="none" stroke="var(--white)" stroke-width="3"/>
    </svg>
    <p class="brand-name">ZELQUIN</p>
    <div class="person">
      <p class="person-name">Alex Moreno Hale</p>
      <p class="person-title">Managing Director</p>
    </div>
    <ul class="contacts">
      <li class="contact-item">555.014.2290
        <svg class="contact-icon" viewBox="0 0 16 16"><circle cx="8" cy="8" r="7" fill="none" stroke="var(--white)" stroke-width="1.2"/><path d="M5.5 4.5 L7 6.5 L6.2 7.4 Q7.2 9 8.6 9.8 L9.5 9 L11.5 10.5 L10.6 11.6 Q6.5 11 4.4 5.4 Z" fill="var(--white)"/></svg>
      </li>
      <li class="contact-item">www.zelquin.com
        <svg class="contact-icon" viewBox="0 0 16 16"><circle cx="8" cy="8" r="7" fill="none" stroke="var(--white)" stroke-width="1.2"/><circle cx="8" cy="8" r="3.8" fill="none" stroke="var(--white)" stroke-width="1"/><path d="M4.2 8 H11.8 M8 4.2 V11.8" stroke="var(--white)" stroke-width="1"/></svg>
      </li>
      <li class="contact-item">alex@zelquin.com
        <svg class="contact-icon" viewBox="0 0 16 16"><circle cx="8" cy="8" r="7" fill="none" stroke="var(--white)" stroke-width="1.2"/><rect x="4.3" y="5.5" width="7.4" height="5" fill="none" stroke="var(--white)" stroke-width="1"/><path d="M4.3 5.5 L8 8.4 L11.7 5.5" fill="none" stroke="var(--white)" stroke-width="1"/></svg>
      </li>
    </ul>
  </section>

</div>
</body>
</html>
```